Business Card Design For A Renovation Contractor Company

We need a business card for a new company based in Singapore, our company name is "RB Tolvane". We are a renovation contractor that builds designs into reality. We build more of F&B restaurants, retail stores and commercial offices. We work very closely with designers. The final design should communicate to our client that we are a company that you can trust, that will plan and complete your project without giving you a headache. I like my client to remember my company as "RB". The beauty of SIMPLE is important.

Industry/Entity Type

Contractor

Requirements
Nice to have
• Black or Red base

```html
<!DOCTYPE html>
<html lang="en">
<head>
<meta charset="utf-8">
<title>RB Tolvane — Business Card</title>
<link href="https://fonts.googleapis.com/css2?family=Open+Sans:wght@400;700&family=Questrial&display=swap" rel="stylesheet">
<style>
  :root {
    --stage: #e9e7e4;
    --paper: #ffffff;
    --ink: #141010;
    --ink-soft: #3a3434;
    --red: #e5202f;
    --white: #ffffff;
  }
  * { margin: 0; padding: 0; box-sizing: border-box; }
  html, body { width: 1200px; height: 720px; overflow: hidden; }
  body {
    background: var(--stage);
    font-family: "Open Sans", Arial, sans-serif;
    position: relative;
  }
  .card {
    position: absolute;
    top: 206px;
    width: 540px;
    height: 309px;
    overflow: hidden;
    box-shadow: 0 6px 18px rgba(0,0,0,0.18);
  }
  .card--front { left: 40px; background: var(--paper); }
  .card--back { left: 620px; background: var(--ink); }

  .front-waves { position: absolute; inset: 0; width: 540px; height: 309px; }

  .holder { position: absolute; top: 20px; right: 24px; text-align: right; }
  .holder__name { font-weight: 700; font-size: 15px; color: var(--ink); }
  .holder__title { font-size: 11px; color: var(--red); }

  .brand { position: absolute; left: 30px; top: 70px; }
  .brand__row { display: flex; align-items: center; gap: 10px; }
  .brand__dot { width: 30px; height: 30px; border-radius: 50%; background: var(--red); }
  .brand__name {
    font-family: "Questrial", "Century Gothic", sans-serif;
    font-size: 40px; line-height: 1; color: var(--red); letter-spacing: -0.5px;
  }
  .brand__tagline {
    margin-top: 4px; padding-top: 2px;
    border-top: 1.5px solid var(--ink-soft);
    font-family: "Questrial", "Century Gothic", sans-serif;
    font-size: 13px; color: var(--ink-soft); letter-spacing: 0.6px;
  }

  .address {
    position: absolute; left: 30px; top: 172px;
    font-size: 11.5px; line-height: 1.4; color: var(--ink-soft);
  }

  .contact {
    position: absolute; right: 20px; top: 134px;
    list-style: none; font-size: 12px; line-height: 1.55; color: var(--white);
  }
  .contact li { display: flex; align-items: center; gap: 6px; }
  .contact svg { width: 10px; height: 10px; flex: none; }

  .back-mark {
    position: absolute; left: 0; right: 0; top: 102px;
    display: flex; justify-content: center; align-items: center; gap: 14px;
  }
  .back-mark__dot { width: 40px; height: 40px; border-radius: 50%; background: var(--white); }
  .back-mark__name {
    font-family: "Questrial", "Century Gothic", sans-serif;
    font-size: 52px; line-height: 1; color: var(--white);
  }
  .back-url {
    position: absolute; left: 0; right: 0; bottom: 52px;
    text-align: center; font-size: 15px; letter-spacing: 4px; color: var(--white);
  }
</style>
</head>
<body>
  <section class="card card--front">
    <svg class="front-waves" viewBox="0 0 540 309" aria-hidden="true">
      <path d="M0,309 L0,300 C150,300 260,280 320,200 C360,140 430,95 540,82 L540,309 Z" fill="var(--ink)"/>
      <path d="M40,304 C190,302 275,272 322,196 C358,138 432,90 540,72" fill="none" stroke="var(--red)" stroke-width="6"/>
      <path d="M90,303 C210,300 285,280 326,204 C360,146 430,100 540,86" fill="none" stroke="var(--red)" stroke-width="2"/>
    </svg>

    <div class="holder">
      <p class="holder__name">Your Name</p>
      <p class="holder__title">Title</p>
    </div>

    <div class="brand">
      <div class="brand__row">
        <span class="brand__dot"></span>
        <span class="brand__name">RB Tolvane</span>
      </div>
      <p class="brand__tagline">designs built right, on plan</p>
    </div>

    <p class="address">Street Name, City Name<br>State Zip Code</p>

    <ul class="contact">
      <li>
        <svg viewBox="0 0 10 10"><circle cx="5" cy="5" r="4.5" fill="none" stroke="currentColor"/><path d="M3.3,2.6 L4.3,3.6 L3.8,4.3 C4.2,5 4.9,5.7 5.6,6.1 L6.3,5.6 L7.3,6.6 L6.6,7.4 C5,7.1 2.9,5 2.6,3.3 Z" fill="currentColor"/></svg>
        123-456-0789
      </li>
      <li>
        <svg viewBox="0 0 10 10"><rect x="2.5" y="0.5" width="5" height="9" rx="1" fill="currentColor"/><rect x="3.3" y="1.6" width="3.4" height="5.4" fill="var(--ink)"/></svg>
        123-456-0789
      </li>
      <li>
        <svg viewBox="0 0 10 10"><rect x="0.5" y="2" width="9" height="6" fill="currentColor"/><path d="M0.5,2 L5,5.5 L9.5,2" fill="none" stroke="var(--ink)" stroke-width="0.8"/></svg>
        info@rbtolvane.com
      </li>
      <li>
        <svg viewBox="0 0 10 10"><circle cx="5" cy="5" r="4.3" fill="none" stroke="currentColor"/><ellipse cx="5" cy="5" rx="1.8" ry="4.3" fill="none" stroke="currentColor" stroke-width="0.7"/><path d="M0.7,5 H9.3" stroke="currentColor" stroke-width="0.7"/></svg>
        www.rbtolvane.com
      </li>
    </ul>
  </section>

  <section class="card card--back">
    <div class="back-mark">
      <span class="back-mark__dot"></span>
      <span class="back-mark__name">RB Tolvane</span>
    </div>
    <p class="back-url">www.rbtolvane.com</p>
  </section>
</body>
</html>
```